High End Cosmetic Packaging Design Project

Looking for packaging for 2 products for a High end skin care line aimed at the 35+ year old women. Color scheme is Pantone 2765c with accents of metallic silver, copper or gold, Pantone colors 871-877c. Possible watermark in the background or a 3D image. We are open to any good ideas and suggestions. Box dimensions for the 2 products are small, approximately 4.375 inches high and 1.5 inches square. I have attached an image of the logo. I have the logo files in all the various forms. 1 box is for a Vitamin C Serum and the other box is for an Anti Aging Serum. Boxes are the same but the text will be different on both products. I will supply the text for the boxes later, including directions & ingredients and a UPC code that has to go on the underside of the box. It has to be an elegant design that will stand out in photos online. Good and quick communication & feedback between you and us is essential. I have attached a jpg of our new logo. I have this logo in all available forms
*****We are open to all ideas and want your ideas and input. The bottles that go inside these boxes are a deep violet almost black tavlen glass. This is where the pantone color selection came from but upon further thought it may not be the right choice. We were out looking at cosmetic packaging today and thought also as an idea that a dark charcoal, or black box might work as well. We have seen boxes in those dark shades in glossy, matt and some with a sparkle finish. Embossed lettering may be a possibility as well. Copper letters may be an idea that works well also. These are just ideas rolling aroung in our heads but please give us your ideas*******
This is for the 35+ year old woman.
Communication

```html
<!DOCTYPE html>
<html lang="en">
<head>
<meta charset="utf-8">
<title>Velane Labs — Serum Carton Dielines</title>
<link rel="stylesheet" href="https://fonts.googleapis.com/css2?family=Raleway:wght@200;300&display=swap">
<style>
  :root {
    --page: #ffffff;
    --silver-deep: #d4d5d8;
    --silver-light: #f3f3f4;
    --silver-line: #c6c6c9;
    --silver-ink: #a3a3a6;
    --gold-deep: #b9ab86;
    --gold-light: #e4ddcc;
    --gold-line: #c3b592;
    --gold-ink: #9c8d66;
  }
  html, body {
    margin: 0;
    padding: 0;
    width: 1200px;
    height: 808px;
    overflow: hidden;
    background: var(--page);
  }
  .sheet {
    display: block;
    width: 1200px;
    height: 808px;
  }
  .cut { fill: none; stroke-width: 1; }
  .carton--silver .cut { stroke: var(--silver-line); }
  .carton--gold .cut { stroke: var(--gold-line); }
  .label {
    font-family: "Raleway", sans-serif;
    font-weight: 200;
  }
  .carton--silver .label { fill: var(--silver-ink); }
  .carton--gold .label { fill: var(--gold-ink); }
  .label--flap { font-size: 14px; letter-spacing: 0.5px; }
  .label--brand { font-size: 16px; letter-spacing: 1px; font-weight: 300; }
  .label--product { font-size: 21px; letter-spacing: 0.5px; }
  .label--serum { font-size: 15.5px; letter-spacing: 0.5px; }
</style>
</head>
<body>
<svg class="sheet" viewBox="0 0 1386 933" xmlns="http://www.w3.org/2000/svg" role="img" aria-label="Flat dielines for two serum cartons">
  <defs>
    <linearGradient id="silverTop" x1="0" y1="0" x2="0" y2="1">
      <stop offset="0" stop-color="#d4d5d8"/>
      <stop offset="1" stop-color="#f3f3f4"/>
    </linearGradient>
    <linearGradient id="silverSide" x1="0" y1="0" x2="0" y2="1">
      <stop offset="0" stop-color="#d4d5d8"/>
      <stop offset="1" stop-color="#f1f1f2"/>
    </linearGradient>
    <linearGradient id="goldTop" x1="0" y1="1" x2="1" y2="0">
      <stop offset="0" stop-color="#e4ddcc"/>
      <stop offset="1" stop-color="#b9ab86"/>
    </linearGradient>
    <linearGradient id="goldSide" x1="0" y1="0" x2="0" y2="1">
      <stop offset="0" stop-color="#b9ab86"/>
      <stop offset="1" stop-color="#e4ddcc"/>
    </linearGradient>
    <linearGradient id="divider" x1="0" y1="0" x2="1" y2="0">
      <stop offset="0" stop-color="#d8d8d8" stop-opacity="0"/>
      <stop offset="0.5" stop-color="#c4c4c4"/>
      <stop offset="1" stop-color="#d8d8d8" stop-opacity="0"/>
    </linearGradient>
  </defs>

  <!-- Vitamin C carton -->
  <g class="carton carton--silver">
    <rect class="panel panel--top" x="253" y="93" width="388" height="197" fill="url(#silverTop)"/>
    <rect class="panel panel--side" x="121" y="290" width="132" height="370" fill="url(#silverSide)"/>
    <g class="dieline">
      <path class="cut" d="M121 290 L78 297 L78 654 L121 660"/>
      <rect class="cut" x="121" y="290" width="520" height="370"/>
      <line class="cut" x1="253" y1="290" x2="253" y2="660"/>
      <line class="cut" x1="383" y1="290" x2="383" y2="660"/>
      <line class="cut" x1="513" y1="290" x2="513" y2="660"/>
      <path class="cut" d="M253 290 L256 278 L266 265 L274 231 L383 231"/>
      <path class="cut" d="M513 231 L624 231 L632 265 L641 278 L641 290"/>
      <path class="cut" d="M383 290 L383 160 L403 160 L403 155 L493 155 L493 160 L513 160 L513 290"/>
      <path class="cut" d="M386 160 L386 155 A62 60 0 0 1 510 155 L510 160"/>
      <path class="cut" d="M253 660 L253 720 L362 720 L370 690 L381 676 L381 660"/>
      <path class="cut" d="M517 660 L517 672 L528 690 L536 720 L626 720 L626 700 L631 690 L641 690 L641 660"/>
      <path class="cut" d="M121 660 L121 790 L141 790 L141 785 L233 785 L233 790 L253 790 L253 660"/>
      <path class="cut" d="M124 790 A62 61 0 0 0 250 790"/>
    </g>
    <text class="label label--flap" transform="rotate(90 446 188)" x="446" y="188">VITAMIN C</text>
    <text class="label label--brand" transform="rotate(90 442 324)" x="442" y="324">VELANE LABS</text>
    <rect class="divider" x="405" y="463" width="95" height="3" fill="url(#divider)"/>
    <text class="label label--product" transform="rotate(90 443 477)" x="443" y="477">VITAMIN C</text>
  </g>

  <!-- Anti Aging carton -->
  <g class="carton carton--gold" transform="translate(644 0)">
    <rect class="panel panel--top" x="253" y="93" width="388" height="197" fill="url(#goldTop)"/>
    <rect class="panel panel--side" x="121" y="290" width="132" height="370" fill="url(#goldSide)"/>
    <g class="dieline">
      <path class="cut" d="M121 290 L78 297 L78 654 L121 660"/>
      <rect class="cut" x="121" y="290" width="520" height="370"/>
      <line class="cut" x1="253" y1="290" x2="253" y2="660"/>
      <line class="cut" x1="383" y1="290" x2="383" y2="660"/>
      <line class="cut" x1="513" y1="290" x2="513" y2="660"/>
      <path class="cut" d="M253 290 L256 278 L266 265 L274 231 L383 231"/>
      <path class="cut" d="M513 231 L624 231 L632 265 L641 278 L641 290"/>
      <path class="cut" d="M383 290 L383 160 L403 160 L403 155 L493 155 L493 160 L513 160 L513 290"/>
      <path class="cut" d="M386 160 L386 155 A62 60 0 0 1 510 155 L510 160"/>
      <path class="cut" d="M253 660 L253 720 L362 720 L370 690 L381 676 L381 660"/>
      <path class="cut" d="M517 660 L517 672 L528 690 L536 720 L626 720 L626 700 L631 690 L641 690 L641 660"/>
      <path class="cut" d="M121 660 L121 790 L141 790 L141 785 L233 785 L233 790 L253 790 L253 660"/>
      <path class="cut" d="M124 790 A62 61 0 0 0 250 790"/>
    </g>
    <text class="label label--flap" transform="rotate(90 446 177)" x="446" y="177">ANTI AGING</text>
    <text class="label label--brand" transform="rotate(90 442 324)" x="442" y="324">VELANE LABS</text>
    <rect class="divider" x="405" y="463" width="95" height="3" fill="url(#divider)"/>
    <text class="label label--serum" transform="rotate(90 446 477)" x="446" y="477">ANTI AGING SERUM</text>
  </g>
</svg>
</body>
</html>
```